Got the awesome logo, now need the awesome business card

Want to use my just purchased logo on the backside of my card and to secure another logo by the same designer (Marcus) for the front side.

Reason: I have uploaded the logos. QVL7 should be on the front of the card with my contact information and Qvl7pex should be on the back. Thank you.

The logos have been uploaded and I have extended the deadline by 5 days. The QVL& logo should be on the front with my contact information and the qvl7pex should be on the back.

• Existing logo(s), clean background on front of card

```html
<!DOCTYPE html>
<html lang="en">
<head>
<meta charset="utf-8">
<title>Qvl7 Business Card</title>
<link rel="stylesheet" href="https://fonts.googleapis.com/css2?family=Open+Sans:wght@400;600;700&display=swap">
<style>
  :root {
    --stage: #d9d9d6;
    --card-blue: #2f7fbf;
    --card-blue-deep: #1f6aa8;
    --card-white: #ffffff;
    --brand-blue: #2d7fc1;
    --brand-orange: #e8822a;
    --ink: #333333;
    --muted: #555555;
    --band: #c9dcee;
    --dot: #bdbdbd;
  }
  * { margin: 0; padding: 0; box-sizing: border-box; }
  html, body {
    width: 1200px;
    height: 871px;
    overflow: hidden;
    background: var(--stage);
    font-family: "Open Sans", sans-serif;
  }
  .canvas {
    position: relative;
    width: 1200px;
    height: 871px;
  }
  .card {
    position: absolute;
    width: 595px;
    height: 340px;
    border-radius: 4px;
    box-shadow: 0 14px 30px rgba(0,0,0,0.25);
    overflow: hidden;
  }
  /* Back side */
  .card-back {
    left: 110px;
    top: 70px;
    background: linear-gradient(160deg, var(--card-blue) 0%, var(--card-blue-deep) 100%);
    display: flex;
    align-items: center;
    justify-content: center;
    gap: 18px;
  }
  .card-back .brand-name {
    font-weight: 700;
    font-size: 78px;
    color: var(--card-white);
    letter-spacing: -1px;
  }
  .card-back .brand-dot {
    width: 22px;
    height: 22px;
    border-radius: 50%;
    background: var(--brand-orange);
  }
  /* Front side */
  .card-front {
    left: 495px;
    top: 460px;
    background: var(--card-white);
  }
  .contact {
    position: absolute;
    left: 40px;
    top: 38px;
    width: 250px;
    color: var(--ink);
  }
  .contact .person {
    font-weight: 700;
    font-size: 15px;
  }
  .contact .role {
    font-size: 13px;
    color: var(--brand-blue);
    margin-top: 2px;
  }
  .contact-list {
    list-style: none;
    margin-top: 30px;
  }
  .contact-list li {
    display: flex;
    align-items: center;
    gap: 12px;
    font-size: 12.5px;
    color: var(--muted);
    height: 21px;
    white-space: nowrap;
  }
  .contact-list svg { flex: none; }
  .social-mark {
    width: 12px;
    height: 12px;
    border-radius: 2px;
    flex: none;
  }
  .social-mark.alt { background: var(--brand-blue); border-radius: 50%; }
  .social-mark.square { background: var(--card-blue-deep); }
  .front-brand {
    position: absolute;
    right: 40px;
    top: 100px;
    display: flex;
    align-items: center;
    gap: 10px;
  }
  .front-brand .brand-name {
    font-weight: 700;
    font-size: 32px;
    line-height: 1.1;
    color: var(--brand-blue);
    text-align: left;
  }
  .front-brand .brand-dot {
    width: 16px;
    height: 16px;
    border-radius: 50%;
    background: var(--brand-orange);
  }
  .base-band {
    position: absolute;
    left: 0;
    right: 0;
    bottom: 0;
    height: 58px;
    background: linear-gradient(90deg, rgba(201,220,238,0.2), var(--band));
  }
  .corner-dot {
    position: absolute;
    right: 22px;
    bottom: 10px;
    width: 40px;
    height: 40px;
    border-radius: 50%;
    background: var(--dot);
  }
</style>
</head>
<body>
  <main class="canvas">
    <section class="card card-back" aria-label="Card back">
      <span class="brand-dot"></span>
      <span class="brand-name">Qvl7pex</span>
    </section>

    <section class="card card-front" aria-label="Card front">
      <div class="contact">
        <p class="person">Elena Varga</p>
        <p class="role">Principal</p>
        <ul class="contact-list">
          <li>
            <svg width="12" height="12" viewBox="0 0 24 24" aria-hidden="true">
              <path fill="var(--brand-orange)" d="M6.6 10.8a15.1 15.1 0 0 0 6.6 6.6l2.2-2.2a1 1 0 0 1 1-.25 11.4 11.4 0 0 0 3.6.57 1 1 0 0 1 1 1V20a1 1 0 0 1-1 1A17 17 0 0 1 3 4a1 1 0 0 1 1-1h3.5a1 1 0 0 1 1 1c0 1.25.2 2.450.57 3.57a1 1 0 0 1-.25 1z"/>
            </svg>
            555.014.2738
          </li>
          <li>
            <svg width="12" height="12" viewBox="0 0 24 24" aria-hidden="true">
              <rect x="2" y="5" width="20" height="14" rx="1.5" fill="none" stroke="var(--brand-orange)" stroke-width="2.4"/>
              <path d="M2.5 6l9.5 7 9.5-7" fill="none" stroke="var(--brand-orange)" stroke-width="2.4"/>
            </svg>
            qvl7mgmt@mailbox.example
          </li>
          <li><span class="social-mark alt"></span>@qvl7management</li>
          <li><span class="social-mark square"></span>ElenaVargaExecMgmt</li>
        </ul>
      </div>

      <div class="front-brand">
        <span class="brand-dot"></span>
        <span class="brand-name">QVL7<br>Management</span>
      </div>

      <div class="base-band"></div>
      <div class="corner-dot"></div>
    </section>
  </main>
</body>
</html>
```